Business card for builder specialising in renovations.

Need a card for our building business. Business name is under Martin Powles.
Have licence number on card ( 527691K)
Contact number (0400 382 415)
Want to work on logo for some business cards and shirts - something with MP or MPB or open to ideas??
No animations, No hammers. Something sharp and eye catching.
Highlight that we are a renovation specialist. Simple on front with extra details on back with some lines to jot down things.

Target Market(s)

Renovators

Industry/Entity Type

Building

Contact Information for Business Card

2 sided with room on back to jot things down.
Extra details on back so front can be simple ..like, renovations, bathrooms, decks, extensions, new builds,

Logo Text

MP

Font styles to use
Serif

Requirements
Must have
• Eye catching design .
• Name : Martin powles
• Licence number
• Contact number - 0400382415
Nice to have
• Some logo design that we can carry through to other forms of advertising
• Local builder
• Quality work
Should not have
• No animations

```html
<!DOCTYPE html>
<html lang="en">
<head>
<meta charset="UTF-8">
<title>Martin Powles – Business Card</title>
<link href="https://fonts.googleapis.com/css2?family=Noto+Serif:wght@400&family=Open+Sans:wght@400;600;700&display=swap" rel="stylesheet">
<style>
  :root {
    --orange: #ec6707;
    --charcoal: #4a4a4a;
    --white: #ffffff;
    --backdrop: #ecebe8;
  }
  * { margin: 0; padding: 0; box-sizing: border-box; }
  html, body {
    width: 1200px; height: 900px; overflow: hidden;
    background: var(--backdrop);
  }
  .canvas { position: relative; width: 1200px; height: 900px; }

  .card { position: absolute; overflow: hidden; box-shadow: 0 4px 14px rgba(0,0,0,.18); }

  /* Front */
  .card-front { left: 78px; top: 35px; width: 587px; height: 362px; background: var(--white); }
  .card-front .shapes { position: absolute; inset: 0; }
  .brand-mark {
    position: absolute; left: 0; right: 0; top: 58px;
    display: flex; justify-content: center; align-items: center; gap: 12px;
  }
  .brand-mark .dot { width: 22px; height: 22px; border-radius: 50%; background: var(--orange); }
  .brand-mark .initials {
    font-family: 'Noto Serif', serif; font-size: 56px; line-height: 1; color: var(--charcoal);
  }
  .front-name {
    position: absolute; left: 0; right: 0; top: 153px; text-align: center;
    font-family: 'Noto Serif', serif; font-size: 40px; line-height: 1;
  }
  .front-name .first { color: var(--orange); }
  .front-name .last { color: var(--charcoal); }
  .contact-name {
    position: absolute; left: 129px; top: 280px;
    font-family: 'Open Sans', sans-serif; font-weight: 700; font-size: 23px; color: var(--white);
  }
  .contact-lines {
    position: absolute; left: 302px; top: 266px;
    font-family: 'Open Sans', sans-serif; font-size: 16px; line-height: 30px; color: var(--white);
  }
  .contact-lines strong { font-weight: 700; }

  /* Back */
  .card-back { left: 388px; top: 505px; width: 567px; height: 352px; background: var(--orange); }
  .back-name {
    position: absolute; left: 0; right: 0; top: 118px; text-align: center;
    font-family: 'Noto Serif', serif; font-size: 48px; line-height: 1; color: var(--white);
  }
  .services-band {
    position: absolute; left: 0; right: 0; top: 218px; height: 59px;
    background: var(--white); display: flex; align-items: center; justify-content: center;
    font-family: 'Open Sans', sans-serif; font-weight: 600; font-size: 16.5px; color: var(--orange);
  }
  .address {
    position: absolute; left: 0; right: 0; top: 298px; text-align: center;
    font-family: 'Open Sans', sans-serif; font-size: 14.5px; color: var(--white);
  }
</style>
</head>
<body>
<main class="canvas">

  <section class="card card-front">
    <svg class="shapes" width="587" height="362" viewBox="0 0 587 362">
      <polygon points="0,220 404,220 382,245 0,245" fill="var(--charcoal)"/>
      <polygon points="0,249 389,249 418,212 587,212 587,362 0,362" fill="var(--orange)"/>
    </svg>
    <div class="brand-mark">
      <span class="dot"></span>
      <span class="initials">MP</span>
    </div>
    <h1 class="front-name"><span class="first">Martin</span> <span class="last">Powles</span></h1>
    <p class="contact-name">Martin Powles</p>
    <div class="contact-lines">
      <p class="phone">0400 382 415</p>
      <p class="licence"><strong>License No-</strong> 527691K</p>
    </div>
  </section>

  <section class="card card-back">
    <h2 class="back-name">Martin Powles</h2>
    <p class="services-band">Rrenovations, bathrooms, decks, extensions, new builds etc</p>
    <p class="address">12345, Address Goes Here Country Name, 123456.</p>
  </section>

</main>
</body>
</html>
```